Velvet Loom (E-commerce) Website for Embroidery shop

Briefing:

Velvet Loom is an online personalized embroidery shop targeting mainly three customer segments:
1) lovers and marring couples
2) close friends wishing to give unique gifts
3) moms with new born baby personalized gifts

These customers are being served through our three major business lines:
1) Bathrobes and towels with personalized embroidery
2) Embroidered pillows and cushions
3) baby gifts with costumed baby sets stitched

Requirements:

The business has been recently established with moderate variety of products introduced so far. The website must consists of four major pages; a home page and three pages for every single business line. All images necessary for the web design are shareable upon request for copyright reasons if necessary. Please post a few products in each page to make it easy for the employee to use as benchmarks to upload other products.

The website also should contain all items and buttons exist in any e-commerce website such as:

1- social links:
a. (Major) Instagram: https://www.instagram.com/velvet.loom.studio/
b. Twitter: https://twitter.com/Velvet_Loom_
c. Facebook: https://www.facebook.com/Velvet.loom.studio/
d. Snapchat: coming soon

2- Help:
a. Delivery & Returns (inside KSA)
I. Delivery:
- Rush: within 3 business days (SAR 90)
- Express: within 5 business days (SAR 65)
- Standard: 7-10 business days ( SAR 35)
II. Returns: We guarantee you will love our product. But if you don't like it, send it back to us within two days from delivery and we will donate it to a charity and return your money subject to our terms and conditions.

b. Contact:
- Email: Velvet.loom.studio@plumemail.net
- (Mobile) Whats-app: +966 54 312 9067 (for quick response)

d. Warranty:
for only SAR 20 per product, we will give you a lifetime warranty over our German stitches

3- Payment options:
bank transfer, visa, MasterCard and PayPal

Remarks:

- This website is mainly aimed at customers in Saudi Arabia where some contents may not appeal to people from such country and results in your participation being excluded from the contest.

- You are the expert and if I am a webdesigner, I would have not posted this contest, so please use your our own judgment and creativity to come up with the best experience possible.

- Use our Instagram account as your first reference to understand our business as it is our major channel that has been used to reach our customers. Please don't use the pictures with poor quality as we will be replacing them with other images with better quality.

- We intend to have this website bilingual (i.e English and Arabic), so if you can translate it into Arabic, then we will pay you an extra $100 in addition to the contest price.

- If in doubt, please feel free to ask any question and suggestions are always encouraged and warm welcomed.

- If you succeed in this contest, you will be chosen as our ultimate Web designer. That means you will have a long relationship providing services to our customers under one of our businesses that aims at preparing start-up companies establishing their business.

Target Market(s)

1) lovers and marrying couples

Industry/Entity Type

Embroidery

Number of Pages Required

4 page

Font styles to use
Serif
Script

Colors

Designer to choose colors to be used in the design.

Requirements
Must have
• Requirements:
• The business has been recently established with moderate variety of products introduced so far. The website must consists of four major pages; a home page and three pages for every single business line. All images necessary for the web design are shareable upon request for copyright reasons if necessary. Please post a few products in each page to make it easy for the employee to use as benchmarks to upload other products.
• The Website must be also mobile use friendly!!!
• The website also should contain all items and buttons exist in any e-commerce website such as:
• 1- social links:
• a. (Major) Instagram: https://www.instagram.com/velvet.loom.studio/
• b. Twitter: https://twitter.com/Velvet_Loom_
• c. Facebook: https://www.facebook.com/Velvet.loom.studio/
• d. Snapchat: coming soon
• 2- Help:
• a. Delivery & Returns (inside KSA)
• I. Delivery:
• - Rush: within 3 business days (SAR 90)
• - Express: within 5 business days (SAR 65)
• - Standard: 7-10 business days ( SAR 35)
• II. Returns: We guarantee you will love our product. But if you don't like it, send it back to us within two days from delivery and we will donate it to a charity and return your money subject to our terms and conditions.
• b. Contact:
• - Email: Velvet.loom.studio@plumemail.net
• - (Mobile) Whats-app: +966 54 312 9067 (for quick response)
• d. Warranty:
• for only SAR 20 per product, we will give you a lifetime warranty over our German stitches
• 3- Payment options:
• bank transfer, visa, MasterCard and PayPal
• Note: You will be responsible to upload the design to the website fully and ensure its integration and functionality.

```html
<!DOCTYPE html>
<html lang="en">
<head>
<meta charset="utf-8">
<title>Velvet Loom — Personalized Embroidery</title>
<link rel="stylesheet" href="https://fonts.googleapis.com/css2?family=Jost:wght@400;500;600&family=Cormorant+Garamond:wght@500&display=swap">
<style>
:root{
  --gold:#c29b52;
  --gold-dark:#a8823c;
  --ink:#333333;
  --muted:#7a7a7a;
  --line:#dddddd;
  --cream:#f8f5ec;
  --btn-gray:#6f7072;
  --topbar:#8e8f92;
  --footer:#9fa1a5;
  --white:#ffffff;
}
*{margin:0;padding:0;box-sizing:border-box}
html,body{width:1200px;height:3442px;overflow:hidden}
body{position:relative;background:var(--white);font-family:"Jost",sans-serif;color:var(--ink)}
.abs{position:absolute}

/* header */
.topbar{left:532px;top:0;width:668px;height:34px;background:var(--topbar);color:var(--white);font-size:11px;display:flex;align-items:center;justify-content:flex-end;gap:26px;padding-right:30px}
.topbar span{display:flex;align-items:center;gap:6px}
.brand{left:131px;top:40px;height:96px;display:flex;align-items:center;gap:12px;white-space:nowrap}
.brand-dot{width:22px;height:22px;border-radius:50%;background:var(--gold);flex:none}
.brand-name{font-family:"Cormorant Garamond",serif;font-weight:500;font-size:36px;color:var(--gold);line-height:1;white-space:nowrap}
.search{left:544px;top:57px;width:300px;height:46px;border:1px solid var(--line);display:flex;align-items:center;gap:10px;padding-left:16px;font-size:10px;letter-spacing:.5px;color:var(--muted)}
.lang{top:64px;height:28px;width:52px;border:1px solid var(--line);font-size:10px;display:flex;align-items:center;justify-content:center;gap:5px;color:var(--ink)}
.flag{width:14px;height:9px;background:#9aa5c4}
.flag.green{background:#3c7a48}
.nav{left:525px;top:126px;display:flex;align-items:center;height:28px;font-size:11px;font-weight:500;letter-spacing:.4px;color:var(--ink)}
.nav a{text-decoration:none;color:inherit;margin-right:34px}
.nav a.active{background:var(--gold);color:var(--white);padding:7px 14px;margin-right:44px}

/* hero */
.hero{left:0;top:172px;width:1200px;height:528px;background:linear-gradient(100deg,#b9b8b6 0%,#e8e6e4 30%,#d9d6d4 48%,#6d6c6c 75%,#8a3a3a 100%)}
.hero-title{left:730px;top:294px;font-size:50px;font-weight:500;line-height:1.15;color:var(--white);letter-spacing:1px}
.hero-btn{left:732px;top:440px;width:172px;height:51px;background:var(--gold);color:var(--white);font-size:15px;font-weight:500;display:flex;align-items:center;justify-content:center;gap:8px}
.dots{left:538px;top:646px;display:flex;gap:12px}
.dots i{width:9px;height:9px;border-radius:50%;background:rgba(255,255,255,.7)}
.dots i:first-child{background:var(--white)}

/* section headings */
.heading{left:0;width:1200px;text-align:center;font-size:27px;font-weight:500;color:var(--gold);letter-spacing:.5px}
.rule{left:570px;width:60px;height:3px;background:#9a9a9a}

/* product cards */
.pcard{top:865px;width:294px;height:385px;border:1px solid #d9c59d}
.pcard .photo{height:275px}
.pcard .name{position:absolute;left:18px;top:292px;font-size:13.5px;line-height:1.55}
.pcard .from{position:absolute;right:18px;top:292px;font-size:9.5px;text-align:right}
.pcard .price{position:absolute;right:18px;top:308px;font-size:22px;font-weight:500;color:var(--gold)}
.outline-btn{position:absolute;left:98px;top:367px;width:104px;height:33px;border:1px solid var(--gold);background:var(--white);color:var(--gold);font-size:12px;font-weight:500;letter-spacing:.5px;display:flex;align-items:center;justify-content:center}

/* welcome */
.welcome{left:131px;top:1450px;width:936px;height:330px;background:var(--cream);border:1px solid #e6dfcc}
.feature{width:250px;display:flex;gap:22px}
.ficon{width:66px;height:66px;border-radius:50%;background:var(--gold);flex:none;display:flex;align-items:center;justify-content:center}
.feature h4{font-size:14.5px;font-weight:400;margin:6px 0 10px}
.feature p{font-size:10.5px;color:var(--muted);line-height:1.6}
.center-brand{left:478px;top:1560px;width:240px;display:flex;align-items:center;justify-content:center;gap:10px}
.center-brand .brand-name{font-size:40px}

/* latest products */
.lcard{top:1975px;width:298px;height:400px;background:var(--cream);border:1px solid #e6dfcc;text-align:center}
.lcard .photo{height:197px}
.lcard .title{margin-top:24px;font-size:14px}
.lcard .price{margin-top:6px;font-size:23px;font-weight:500;color:var(--gold)}
.stars{margin-top:4px;color:var(--gold);font-size:13px;letter-spacing:3px}
.gray-btn{display:inline-flex;align-items:center;justify-content:center;width:120px;height:37px;background:var(--btn-gray);color:var(--white);font-size:12px;font-weight:500;letter-spacing:.5px}
.lcard .gray-btn{margin-top:14px}

/* blog */
.bcard{top:2562px;width:298px;height:398px;border:1px solid #e2e2e2;background:var(--white)}
.bcard .photo{height:195px}
.bcard .date{position:absolute;left:8px;top:186px;background:var(--white);font-size:9px;padding:3px 10px;border:1px solid #e2e2e2}
.bcard h3{position:absolute;left:22px;top:234px;width:258px;font-size:14.5px;font-weight:500;line-height:1.45}
.bcard p{position:absolute;left:22px;top:290px;width:250px;font-size:10.5px;color:#555;line-height:1.65}
.bcard .gray-btn{position:absolute;left:22px;top:338px;width:106px;height:35px;font-size:11px}

/* footer */
.footer{left:0;top:3026px;width:1200px;height:416px;background:var(--footer);color:var(--white)}
.footer h5{font-size:12px;font-weight:500;letter-spacing:.6px}
.footer .col p{font-size:10.5px;line-height:2.05}
.crow{display:flex;gap:16px;font-size:10.5px;line-height:1.7;margin-bottom:20px}
.social{display:flex;gap:10px;align-items:center}
.social i{width:30px;height:30px;border-radius:50%;background:var(--white);opacity:.9}
.pay{display:flex;gap:8px}
.pay i{width:46px;height:28px;background:#e9e9ea;border-radius:2px}
.divider{left:131px;top:3338px;width:938px;height:1px;background:rgba(255,255,255,.5)}
</style>
</head>
<body>

<header>
  <div class="abs topbar">
    <span><svg width="12" height="9" viewBox="0 0 12 9"><rect x=".5" y=".5" width="11" height="8" fill="none" stroke="#fff"/><path d="M.5 .5 6 5l5.5-4.5" fill="none" stroke="#fff"/></svg>Velvet.loom.studio@plumemail.net</span>
    <span><svg width="10" height="10" viewBox="0 0 10 10"><path d="M2 0l2 2.5-1 1.2c.6 1.3 1.4 2.1 2.7 2.7l1.2-1 2.6 2L8.4 10C3.7 9.5.5 6.3 0 1.6z" fill="#fff"/></svg>+966 54 312 9067</span>
    <span><svg width="12" height="10" viewBox="0 0 12 10"><path d="M0 1h2l1.6 6h6.4L12 2.5H3" fill="none" stroke="#fff"/><circle cx="4.5" cy="9" r="1" fill="#fff"/><circle cx="9" cy="9" r="1" fill="#fff"/></svg>My Cart (0)</span>
    <span><svg width="10" height="10" viewBox="0 0 10 10"><circle cx="5" cy="3" r="2.5" fill="#fff"/><path d="M0 10c0-3 2.2-4.5 5-4.5S10 7 10 10z" fill="#fff"/></svg>My Account</span>
  </div>

  <div class="abs brand"><span class="brand-dot"></span><span class="brand-name">Velvet Loom</span></div>

  <div class="abs search">
    <svg width="12" height="12" viewBox="0 0 12 12"><circle cx="5" cy="5" r="4" fill="none" stroke="#777" stroke-width="1.4"/><path d="M8 8l3.5 3.5" stroke="#777" stroke-width="1.4"/></svg>
    SEARCH PRODUCTS
  </div>
  <div class="abs lang" style="left:952px"><span class="flag"></span>EN</div>
  <div class="abs lang" style="left:1012px"><span class="flag green"></span>Ar</div>

  <nav class="abs nav">
    <a class="active" href="#">HOME</a>
    <a href="#">ABOUT US</a>
    <a href="#">SERVICES</a>
    <a href="#">PRODUCTS</a>
    <a href="#">BLOG</a>
    <a href="#" style="margin-right:0">CONTACT US</a>
  </nav>
</header>

<section>
  <div class="abs hero" role="img" aria-label="Embroidered white pillow with a pink date calendar stitched on it, resting on sequined fabric beside red letters"></div>
  <h1 class="abs hero-title">EMBROIDERED<br>PILLOWS</h1>
  <div class="abs hero-btn">READ MORE
    <svg width="12" height="10" viewBox="0 0 12 10"><path d="M1 1l4 4-4 4M6 1l4 4-4 4" fill="none" stroke="#fff" stroke-width="1.6"/></svg></div>
  <div class="abs dots"><i></i><i></i><i></i><i></i><i></i></div>
</section>

<section>
  <h2 class="abs heading" style="top:755px">OUR PRODUCTS</h2>
  <div class="abs rule" style="top:806px"></div>

  <article class="abs pcard" style="left:131px">
    <div class="photo" role="img" aria-label="Red and white bathrobes and towels embroidered with names" style="background:linear-gradient(135deg,#e9dccb,#c83a2c 55%,#f1ece6)"></div>
    <div class="name">Bathrobes<br>and towels</div>
    <div class="from">STARTING FROM</div>
    <div class="price">$15.99</div>
    <div class="outline-btn">BUY NOW</div>
  </article>
  <article class="abs pcard" style="left:452px">
    <div class="photo" role="img" aria-label="White cushion embroidered with a purple calendar and a name" style="background:linear-gradient(135deg,#2b2b2d,#eeeaee 45%,#d9d3da 80%,#3a3a3c)"></div>
    <div class="name">Embroidered<br>pillows and cushions</div>
    <div class="from">STARTING FROM</div>
    <div class="price">$25.99</div>
    <div class="outline-btn">BUY NOW</div>
  </article>
  <article class="abs pcard" style="left:773px">
    <div class="photo" role="img" aria-label="Baby outfit set in white and pink on a yellow blanket" style="background:linear-gradient(135deg,#ece37a,#f3efe6 45%,#eaa6a6 80%)"></div>
    <div class="name">Baby gifts with<br>costumed baby sets</div>
    <div class="from">STARTING FROM</div>
    <div class="price">$18.99</div>
    <div class="outline-btn">BUY NOW</div>
  </article>
</section>

<section>
  <h2 class="abs heading" style="top:1342px">WELCOME TO OUR SITE</h2>
  <div class="abs rule" style="top:1394px"></div>

  <div class="abs welcome"></div>
  <svg class="abs" style="left:131px;top:1450px" width="936" height="330" viewBox="0 0 936 330">
    <g fill="none" stroke="#9a9a9a" stroke-width="1">
      <path d="M349 53H412V120H355"/><path d="M349 315H412V230H355"/>
      <path d="M587 53H520V120H580"/><path d="M587 315H520V230H580"/>
    </g>
    <g fill="#8a8a8a"><circle cx="349" cy="53" r="4"/><circle cx="349" cy="315" r="4"/><circle cx="587" cy="53" r="4"/><circle cx="587" cy="315" r="4"/></g>
  </svg>
  <div class="abs center-brand"><span class="brand-dot"></span><span class="brand-name">Velvet Loom</span></div>

  <div class="abs feature" style="left:174px;top:1506px">
    <div class="ficon"><svg width="28" height="28" viewBox="0 0 28 28"><path d="M5 17v-3a9 9 0 0118 0v3" fill="none" stroke="#fff" stroke-width="2.2"/><rect x="3" y="15" width="5" height="8" rx="1.5" fill="#fff"/><rect x="20" y="15" width="5" height="8" rx="1.5" fill="#fff"/></svg></div>
    <div><h4>Support</h4><p>Passages of Lorem Ipsum available,<br>but the majority.</p></div>
  </div>
  <div class="abs feature" style="left:174px;top:1648px">
    <div class="ficon"><svg width="28" height="28" viewBox="0 0 28 28"><path d="M9 4v20M14 4v20M19 4v20" stroke="#fff" stroke-width="2.4" stroke-linecap="round"/></svg></div>
    <div><h4>Quality work</h4><p>Passages of Lorem Ipsum available,<br>but the majority.</p></div>
  </div>
  <div class="abs feature" style="left:746px;top:1506px">
    <div class="ficon"><svg width="30" height="24" viewBox="0 0 30 24"><rect x="2" y="4" width="16" height="12" fill="#fff"/><path d="M18 8h6l4 4v4H18z" fill="#fff"/><circle cx="8" cy="19" r="3" fill="#fff"/><circle cx="23" cy="19" r="3" fill="#fff"/></svg></div>
    <div><h4>Free Shipping</h4><p>Passages of Lorem Ipsum available,<br>but the majority.</p></div>
  </div>
  <div class="abs feature" style="left:746px;top:1648px">
    <div class="ficon"><svg width="30" height="26" viewBox="0 0 30 26"><circle cx="15" cy="7" r="4" fill="#fff"/><circle cx="6" cy="10" r="3" fill="#fff"/><circle cx="24" cy="10" r="3" fill="#fff"/><path d="M8 22c0-5 3-8 7-8s7 3 7 8zM1 21c0-4 2-6 5-6 1.5 0 2.5.5 3 1.2-1 1.4-1.5 3-1.6 4.8zM29 21c0-4-2-6-5-6-1.5 0-2.5.5-3 1.2 1 1.4 1.5 3 1.6 4.8z" fill="#fff"/></svg></div>
    <div><h4>Professional Team</h4><p>Passages of Lorem Ipsum available,<br>but the majority.</p></div>
  </div>
</section>

<section>
  <h2 class="abs heading" style="top:1854px">LATEST PRODUCTS</h2>
  <div class="abs rule" style="top:1906px"></div>

  <article class="abs lcard" style="left:131px">
    <div class="photo" role="img" aria-label="Red and white towels embroidered with names" style="background:linear-gradient(135deg,#efe6dc,#c5362c 55%,#e9e2da)"></div>
    <div class="title">Lorem Ipsum is simply</div>
    <div class="price">$15.99</div>
    <div class="stars">★★★★★</div>
    <div class="gray-btn">BUY NOW</div>
  </article>
  <article class="abs lcard" style="left:451px">
    <div class="photo" role="img" aria-label="Navy and white towels embroidered with initials" style="background:linear-gradient(135deg,#d8d8dc,#2f3a66 50%,#c9c6d2)"></div>
    <div class="title">It is a long established</div>
    <div class="price">$25.99</div>
    <div class="stars">★★★★★</div>
    <div class="gray-btn">BUY NOW</div>
  </article>
  <article class="abs lcard" style="left:770px">
    <div class="photo" role="img" aria-label="Coral and patterned towels embroidered with names" style="background:linear-gradient(135deg,#f07c74,#f2ecea 50%,#8a9bc2)"></div>
    <div class="title">There are many variations of</div>
    <div class="price">$32.99</div>
    <div class="stars">★★★★★</div>
    <div class="gray-btn">BUY NOW</div>
  </article>
</section>

<section>
  <h2 class="abs heading" style="top:2448px">LATEST BLOG</h2>
  <div class="abs rule" style="top:2500px"></div>

  <article class="abs bcard" style="left:131px">
    <div class="photo" role="img" aria-label="Colourful hooded baby towels folded together" style="background:linear-gradient(135deg,#f0a8c6,#e7c34e 45%,#6fb6d2 85%)"></div>
    <div class="date">April 15,2017</div>
    <h3>There are many variations of pass of Lorem Ipsum available</h3>
    <p>It is a long established fact that a re ader will be distracted by the readable</p>
    <div class="gray-btn">READ MORE</div>
  </article>
  <article class="abs bcard" style="left:451px">
    <div class="photo" role="img" aria-label="Brown towels embroidered with a gold name" style="background:linear-gradient(135deg,#b9b4ad,#6d5d50 50%,#9b8b80)"></div>
    <div class="date">April 15,2017</div>
    <h3>Lorem Ipsum is simply dummy text of the printing</h3>
    <p>It is a long established fact that a re ader will be distracted by the readable</p>
    <div class="gray-btn">READ MORE</div>
  </article>
  <article class="abs bcard" style="left:770px">
    <div class="photo" role="img" aria-label="Baby towels embroidered with an initial and small car motif" style="background:linear-gradient(135deg,#f1efec,#b9c4d8 50%,#d36868 85%)"></div>
    <div class="date">April 15,2017</div>
    <h3>But I must explain to you how all this mistaken idea</h3>
    <p>It is a long established fact that a re ader will be distracted by the readable</p>
    <div class="gray-btn">READ MORE</div>
  </article>
</section>

<footer class="abs footer">
  <div class="abs" style="left:180px;top:120px;display:flex;align-items:center;gap:10px;white-space:nowrap">
    <span class="brand-dot" style="background:var(--white)"></span>
    <span class="brand-name" style="color:var(--white)">Velvet Loom</span>
  </div>
  <div class="abs" style="left:174px;top:242px;display:flex;align-items:center;gap:14px">
    <h5>FOLLOW US</h5>
    <div class="social" role="list">
      <i role="img" aria-label="Social link one"></i><i role="img" aria-label="Social link two"></i><i role="img" aria-label="Social link three"></i>
    </div>
  </div>

  <div class="abs col" style="left:507px;top:66px">
    <h5 style="margin-bottom:22px">CONTACT US</h5>
    <div class="crow"><svg width="10" height="13" viewBox="0 0 10 13"><path d="M5 0a5 5 0 015 5c0 3.5-5 8-5 8S0 8.5 0 5a5 5 0 015-5z" fill="#fff"/><circle cx="5" cy="5" r="1.8" fill="#9fa1a5"/></svg><span>27 Cedar Row Lane<br>Riyadh 12244</span></div>
    <div class="crow"><svg width="11" height="11" viewBox="0 0 10 10"><path d="M2 0l2 2.5-1 1.2c.6 1.3 1.4 2.1 2.7 2.7l1.2-1 2.6 2L8.4 10C3.7 9.5.5 6.3 0 1.6z" fill="#fff"/></svg><span>+966 54 312 9067</span></div>
    <div class="crow"><svg width="12" height="9" viewBox="0 0 12 9"><rect x=".5" y=".5" width="11" height="8" fill="none" stroke="#fff"/><path d="M.5 .5 6 5l5.5-4.5" fill="none" stroke="#fff"/></svg><span>Velvet.loom.studio@plumemail.net</span></div>
  </div>

  <div class="abs col" style="left:821px;top:66px">
    <h5 style="margin-bottom:18px">LINKS</h5>
    <p>My Account<br>Login<br>Register<br>My Cart<br>Wishlist<br>FAQ</p>
  </div>
  <div class="abs col" style="left:1005px;top:66px">
    <h5 style="margin-bottom:18px">MENU</h5>
    <p>Home<br>About us<br>Services<br>Products<br>Blog<br>Contact us</p>
  </div>

  <div class="abs" style="left:131px;top:344px;display:flex;align-items:center;gap:16px">
    <h5>WE ACCEPT</h5>
    <div class="pay"><i role="img" aria-label="Payment method one"></i><i role="img" aria-label="Payment method two"></i><i role="img" aria-label="Payment method three"></i><i role="img" aria-label="Bank transfer"></i></div>
  </div>
  <div class="abs" style="left:892px;top:352px;font-size:9.5px">Copyright © 2017 All Rights Reserved</div>
</footer>
<div class="abs divider"></div>

</body>
</html>
```